Very new and innovative Web design for Property managers of Vacation rentals

We are looking for a new website design for travel agencies and property managers specialised on vacation rentals business, holiday villas and apartments.

The end users of this website are travellers who are looking for a vacation home for their next holiday: this is the reason why the website must be easy to use, attractive, professional, possibly elegant and focused on get new reservations.

This is a draft of our current website: https://intro3.kelumsito.com/
Please consider that we would like to have proposals with a totally different and innovative layout, surprise us!

These are the pages of the website:
• Homepage: feel free to redesign all the homepage as you wish, surprise us with something very new! Please consider that Property manager/Travel agencies usually want to have the opportunity to put in evidence groups of houses with specific characteristics (eg. villas with private swimming pool, apartment in big/small towns, villas with air co, etc…), destinations and tourist areas, and sometimes experiences or activities (please consider that the website layout must be suitable even if some of the previous sections are not used).
• Search page: we’d like to organise the results of the search page in three different ways:
o Grid
o Map
o List
• Property page: to illustrate the characteristics, descriptions, images, …. of the property. It is very important to put in evidence images of the property and to maintain the booking form (and the other call to action bottom – eg. whatsapp) always visible
• Custom pages: static pages composed usually by text, images and call to actions
• Contact us (general form)
• Info request (specific of a property form)
• Booking process
• Blog, organised in four pages:
o Home Page – introduction to the blog
o List of articles
o Single article
o Site Map (presentation of categories and sub-categories)

If possible, we’d prefer to receive the material in Adobe XD or similar so that we can obtain the three versions:
- smartphone
- tablet
- desktop

The website will be then developed in Bootstrap: as a result we’ll need the icons in SVG format (or the library used)

In attachment you can find the map of the website pages

```html
<!DOCTYPE html>
<html lang="en">
<head>
<meta charset="utf-8">
<title>HolidayNest – Desktop and Mobile Layouts</title>
<link rel="stylesheet" href="https://fonts.googleapis.com/css2?family=Playfair+Display:wght@400;700&family=Open+Sans:wght@400;600;700&display=swap">
<style>
:root{
  --board:#5c7a6f;
  --green:#1fbf8f;
  --ink:#1f2b2a;
  --dark:#232b2b;
  --darker:#1a2020;
  --muted:#6f7a78;
  --line:#e1e6e4;
  --paper:#ffffff;
  --soft:#f3f5f4;
  --serif:'Playfair Display', Georgia, serif;
  --sans:'Open Sans', Arial, sans-serif;
}
*{box-sizing:border-box;margin:0;padding:0}
html,body{width:1200px;height:3000px;overflow:hidden}
body{position:relative;background:var(--board);font-family:var(--sans);color:var(--ink);line-height:1.45}
ul{list-style:none}
.photo{display:block;border-radius:2px}
.btn{display:inline-block;background:var(--green);color:#fff;font-weight:600;border-radius:2px;white-space:nowrap}
.field{border:1px solid var(--line);background:#fff;display:flex;align-items:center;color:var(--muted)}
.kicker{display:block;color:var(--green);text-transform:uppercase;letter-spacing:1px}

/* board labels */
.board-label{position:absolute;font-family:var(--serif);font-weight:700;color:#fff;font-size:44px;writing-mode:vertical-rl;white-space:nowrap}
.label-desktop{left:22px;top:860px;transform:rotate(180deg)}
.label-mobile{left:1136px;top:70px}

/* ============ desktop page ============ */
.desktop{position:absolute;left:100px;top:60px;width:760px;background:var(--paper);font-size:11px}
.desktop h2{font-family:var(--serif);font-weight:700;font-size:24px;text-align:center;line-height:1.2}
.desktop .btn{font-size:9.5px;padding:5px 12px}
.desktop .kicker{font-size:9px;text-align:center;margin-bottom:2px}

.d-header{height:44px;display:flex;align-items:center;justify-content:space-between;padding:0 30px;border-top:3px solid var(--green)}
.brand{display:flex;align-items:center;gap:7px;font-weight:700;color:var(--ink)}
.brand-dot{background:var(--green);border-radius:50%;flex:none}
.d-header .brand{font-size:14px}
.d-header .brand-dot{width:16px;height:16px}
.d-nav{display:flex;gap:18px;font-size:10px;font-weight:600}
.d-nav .active{color:var(--green)}

.d-hero{position:relative;height:230px;background:linear-gradient(120deg,#5e8aa6 0%,#7fa9b8 35%,#5d7f57 65%,#3f5b3a 100%)}
.d-hero-text{position:absolute;left:30px;top:78px;color:#fff}
.d-hero-text small{font-size:11px}
.d-hero-text h1{font-family:var(--serif);font-size:36px;line-height:1.1;font-weight:700}
.d-search{position:absolute;right:30px;top:28px;width:240px;background:#fff;padding:14px;border-radius:3px;box-shadow:0 6px 18px rgba(0,0,0,.2)}
.d-search h3{font-family:var(--serif);font-size:14px;margin-bottom:8px}
.d-search .field{height:24px;padding:0 8px;font-size:9px;margin-bottom:7px}
.field-row{display:flex;gap:7px}.field-row .field{flex:1}
.d-search .btn{display:block;text-align:center;padding:6px}

.d-best{padding:28px 30px 30px}
.d-best .sub{text-align:center;color:var(--muted);font-size:9.5px;margin:3px 0 16px}
.d-row{display:flex;gap:20px}
.d-row > *{flex:1}
.d-opp .photo{height:110px}
.d-opp p{text-align:center;font-weight:600;font-size:10.5px;margin-top:7px}

.d-exclusive{display:flex;height:220px;background:var(--soft)}
.d-exclusive-panel{width:280px;background:var(--dark);color:#fff;padding:40px 26px 0 30px}
.d-exclusive-panel small{color:var(--green);font-size:10px}
.d-exclusive-panel h2{color:#fff;text-align:left;margin:2px 0 10px}
.d-exclusive-panel p{color:#c8d0ce;font-size:9.5px;margin-bottom:14px}
.d-exclusive .photo{flex:1;margin:20px 30px 20px 0;border-radius:0}

.d-destinations{padding:30px}
.d-destinations h2{margin-bottom:18px}
.d-grid{display:grid;grid-template-columns:repeat(3,1fr);gap:18px 20px}
.d-dest .photo{height:100px}
.d-dest h4{font-size:11px;margin-top:6px}
.d-dest p{color:var(--muted);font-size:9px;margin-bottom:6px}

.d-rentals{padding-top:6px}
.d-rentals h2{margin-bottom:14px}
.d-strip{display:flex;height:110px}
.d-strip .photo{flex:1;border-radius:0}

.d-experiences{display:flex;gap:26px;padding:30px}
.d-exp-head{width:210px;flex:none}
.d-exp-head .kicker,.d-exp-head h2{text-align:left}
.d-exp-head p{color:var(--muted);font-size:9.5px;margin-top:8px}
.d-exp-grid{flex:1;display:grid;grid-template-columns:1fr 1fr;gap:18px 20px;align-content:start;padding-top:6px}
.exp{display:flex;gap:10px;align-items:flex-start}
.exp-icon{flex:none;border-radius:50%;background:var(--green);display:flex;align-items:center;justify-content:center}
.d-exp-grid .exp-icon{width:32px;height:32px}
.d-exp-grid h4{font-size:11px}
.d-exp-grid p{color:var(--muted);font-size:9px}

.d-blog{padding:6px 30px 30px}
.d-blog h2{margin-bottom:16px}
.d-post .photo{height:100px}
.d-post h4{font-size:11px;margin-top:8px}
.d-post p{color:var(--muted);font-size:9px;margin:2px 0 8px}

.d-contact{padding:0 30px 30px}
.d-contact h2{margin-bottom:12px}
.d-form{width:440px;margin:0 auto;display:grid;grid-template-columns:1fr 1fr;gap:8px}
.d-form .field{height:26px;padding:0 8px;font-size:9px}
.d-form .msg{grid-column:1/3;height:40px}
.d-form .btn{grid-column:2/3;justify-self:end}

.d-footer{background:var(--darker);color:#cfd6d4;padding:28px 30px 14px}
.d-footer-cols{display:flex;justify-content:space-between}
.d-footer .brand{color:#fff;font-size:14px}
.d-footer .brand-dot{width:16px;height:16px}
.f-col h5{color:#fff;font-size:10px;margin-bottom:5px}
.f-col li{font-size:9px;line-height:1.8;display:flex;align-items:center;gap:6px}
.social-dot{width:10px;height:10px;border-radius:50%;background:var(--green)}
.copyright{border-top:1px solid #34403f;margin-top:16px;padding-top:10px;font-size:9px;text-align:center;color:#8b9694}

/* ============ mobile page ============ */
.mobile{position:absolute;left:900px;top:60px;width:220px;background:var(--paper);font-size:8.5px}
.mobile h2{font-family:var(--serif);font-weight:700;font-size:15px;text-align:center;line-height:1.2}
.mobile .btn{font-size:8px;padding:4px 9px}
.mobile .kicker{font-size:7px;text-align:center}
.m-section{padding:16px 12px}

.m-header{height:30px;display:flex;align-items:center;justify-content:space-between;padding:0 12px;border-top:2px solid var(--green)}
.m-header .brand{font-size:10px;gap:5px}
.m-header .brand-dot{width:11px;height:11px}

.m-hero{height:120px;background:linear-gradient(120deg,#5e8aa6,#7fa9b8 40%,#5d7f57 75%,#3f5b3a);color:#fff;padding:42px 12px 0}
.m-hero small{font-size:8px}
.m-hero h1{font-family:var(--serif);font-size:20px;line-height:1.1}
.m-search{background:var(--dark);padding:10px 12px 12px}
.m-search h3{font-family:var(--serif);color:#fff;font-size:11px;margin-bottom:6px}
.m-search .field{height:20px;padding:0 6px;font-size:7.5px;margin-bottom:5px}
.m-search .field-row{gap:5px}
.m-search .btn{display:block;text-align:center;padding:5px}

.m-best .photo{height:110px;margin-top:10px}
.m-best p{text-align:center;font-weight:600;font-size:9px;margin-top:6px}
.dots{display:flex;justify-content:center;gap:5px;margin-top:8px}
.dots span{width:6px;height:6px;border-radius:50%;background:var(--line)}
.dots .on{background:var(--green)}

.m-exclusive{background:var(--dark);color:#fff;padding:18px 12px}
.m-exclusive small{color:var(--green);font-size:8px}
.m-exclusive h2{color:#fff;text-align:left;margin:2px 0 6px}
.m-exclusive p{color:#c8d0ce;font-size:8px;margin-bottom:10px}
.m-exclusive .photo{height:120px;margin-top:12px}

.m-dest .photo{height:130px;margin:10px 0 6px}
.m-dest h4{font-size:9.5px}
.m-dest p{color:var(--muted);font-size:7.5px;margin-bottom:6px}

.m-rentals h2{margin-bottom:10px}
.m-rentals .photo{height:120px;margin-bottom:6px;position:relative}
.m-rentals .tag{position:absolute;left:8px;bottom:8px;color:#fff;font-family:var(--serif);font-weight:700;font-size:11px}

.m-exp h2{margin-bottom:10px}
.m-exp .exp{margin-bottom:10px}
.m-exp .exp-icon{width:22px;height:22px}
.m-exp h4{font-size:9px}
.m-exp p{color:var(--muted);font-size:7.5px}

.m-blog .photo{height:110px;margin:10px 0 6px}
.m-blog h4{font-size:9.5px}
.m-blog p{color:var(--muted);font-size:7.5px;margin-bottom:6px}

.m-contact h2{margin-bottom:10px}
.m-contact .field{height:22px;padding:0 6px;font-size:7.5px;margin-bottom:6px}
.m-contact .msg{height:40px;align-items:flex-start;padding-top:5px}
.m-contact .btn{float:right}
.m-contact::after{content:"";display:block;clear:both}

.m-footer{background:var(--darker);color:#cfd6d4;padding:16px 12px 12px}
.m-footer .f-col{margin-bottom:12px}
.m-footer .f-col h5{font-size:9px}
.m-footer .f-col li{font-size:7.5px}
.m-footer .social-dot{width:8px;height:8px}
.m-footer .brand{color:#fff;font-size:10px;justify-content:center;margin-top:4px}
.m-footer .brand-dot{width:11px;height:11px}
</style>
</head>
<body>

<span class="board-label label-desktop">Desktop Version</span>
<span class="board-label label-mobile">Mobile Version</span>

<!-- desktop layout -->
<main class="desktop">
  <header class="d-header">
    <div class="brand"><span class="brand-dot"></span>HolidayNest</div>
    <nav class="d-nav"><span class="active">Home</span><span>Destinations</span><span>Villas</span><span>Experiences</span><span>Blog</span><span>Contact</span></nav>
    <span class="btn">Book Now</span>
  </header>

  <section class="d-hero" role="img" aria-label="Lakeside Italian village with villas and mountains">
    <div class="d-hero-text"><small>Holidays &amp; Vacation Homes</small><h1>Villas in Italy</h1></div>
    <div class="d-search">
      <h3>Find your Villa</h3>
      <div class="field">Destination</div>
      <div class="field-row"><div class="field">Check-in</div><div class="field">Check-out</div></div>
      <div class="field">Guests</div>
      <span class="btn">Search</span>
    </div>
  </section>

  <section class="d-best">
    <h2>Best Opportunity</h2>
    <p class="sub">Hand-picked homes for every kind of holiday</p>
    <div class="d-row">
      <div class="d-opp"><div class="photo" role="img" aria-label="Villa with private swimming pool" style="background:linear-gradient(135deg,#c9a77e,#7ab3c8)"></div><p>Villas with Private Pool</p></div>
      <div class="d-opp"><div class="photo" role="img" aria-label="Apartment in a small Italian town" style="background:linear-gradient(135deg,#b98f68,#d9c3a0)"></div><p>Apartments in Small Towns</p></div>
      <div class="d-opp"><div class="photo" role="img" aria-label="Bright villa bedroom" style="background:linear-gradient(135deg,#e6dccb,#a8b6a2)"></div><p>Villas with Air Conditioning</p></div>
    </div>
  </section>

  <section class="d-exclusive">
    <div class="d-exclusive-panel">
      <small>Looking for an</small>
      <h2>Exclusive Holiday?</h2>
      <p>Discover our selection of luxury villas by the sea, with private pools, stunning views and tailored services.</p>
      <span class="btn">Discover More</span>
    </div>
    <div class="photo" role="img" aria-label="Castle on a cliff above a turquoise bay" style="background:linear-gradient(160deg,#9bc3d6 0%,#c7b28e 45%,#2e8fa6 100%)"></div>
  </section>

  <section class="d-destinations">
    <h2>Destinations &amp; Tourist Areas</h2>
    <div class="d-grid">
      <div class="d-dest"><div class="photo" role="img" aria-label="Ancient amphitheatre" style="background:linear-gradient(135deg,#c9a074,#8fb1c9)"></div><h4>Rome &amp; Lazio</h4><p>History, art and fine food</p><span class="btn">Discover</span></div>
      <div class="d-dest"><div class="photo" role="img" aria-label="Tuscan town square" style="background:linear-gradient(135deg,#d8cdb8,#86a8c4)"></div><h4>Tuscany</h4><p>Rolling hills and vineyards</p><span class="btn">Discover</span></div>
      <div class="d-dest"><div class="photo" role="img" aria-label="Coastal village by the sea" style="background:linear-gradient(135deg,#d0a57a,#4d7f9a)"></div><h4>Amalfi Coast</h4><p>Colourful villages by the sea</p><span class="btn">Discover</span></div>
      <div class="d-dest"><div class="photo" role="img" aria-label="Historic stone facade" style="background:linear-gradient(135deg,#c48b62,#e0b98f)"></div><h4>Sicily</h4><p>Temples, beaches and sun</p><span class="btn">Discover</span></div>
      <div class="d-dest"><div class="photo" role="img" aria-label="Canal with old palaces" style="background:linear-gradient(135deg,#9cbfd6,#d6c7a6)"></div><h4>Venice</h4><p>Canals and timeless charm</p><span class="btn">Discover</span></div>
      <div class="d-dest"><div class="photo" role="img" aria-label="Illuminated church at night" style="background:linear-gradient(135deg,#2b3f6a,#d49a52)"></div><h4>Lake Como</h4><p>Elegant villas on the water</p><span class="btn">Discover</span></div>
    </div>
  </section>

  <section class="d-rentals">
    <span class="kicker">Our Villas in</span>
    <h2>Vacation Rentals</h2>
    <div class="d-strip">
      <div class="photo" role="img" aria-label="Villa pool at sunset" style="background:linear-gradient(135deg,#3d7fa3,#d8a870)"></div>
      <div class="photo" role="img" aria-label="Stone villa with garden" style="background:linear-gradient(135deg,#b6a184,#6e8f5a)"></div>
      <div class="photo" role="img" aria-label="Infinity pool overlooking the sea" style="background:linear-gradient(135deg,#5fb6cf,#2f6f8e)"></div>
      <div class="photo" role="img" aria-label="Luxury villa interior" style="background:linear-gradient(135deg,#d9c7a8,#8b7257)"></div>
    </div>
  </section>

  <section class="d-experiences">
    <div class="d-exp-head">
      <span class="kicker">Live Italy</span>
      <h2>Experiences or Activities</h2>
      <p>Make your holiday unforgettable with local tours, tastings and outdoor adventures.</p>
    </div>
    <div class="d-exp-grid">
      <div class="exp"><span class="exp-icon"><svg width="14" height="14" viewBox="0 0 20 20"><path d="M10 2a6 6 0 0 1 6 6c0 4.5-6 10-6 10S4 12.5 4 8a6 6 0 0 1 6-6z" fill="none" stroke="#fff" stroke-width="2"/><circle cx="10" cy="8" r="2" fill="#fff"/></svg></span><div><h4>Guided Tours</h4><p>Explore towns with local experts</p></div></div>
      <div class="exp"><span class="exp-icon"><svg width="14" height="14" viewBox="0 0 20 20"><path d="M4 10l4 4 8-8" fill="none" stroke="#fff" stroke-width="2.4"/></svg></span><div><h4>Wine &amp; Food Tasting</h4><p>Taste regional wines and dishes</p></div></div>
      <div class="exp"><span class="exp-icon"><svg width="14" height="14" viewBox="0 0 20 20"><circle cx="10" cy="10" r="7" fill="none" stroke="#fff" stroke-width="2"/><path d="M10 6v4l3 2" stroke="#fff" stroke-width="2" fill="none"/></svg></span><div><h4>Boat Trips</h4><p>Sail along the coastline</p></div></div>
      <div class="exp"><span class="exp-icon"><svg width="14" height="14" viewBox="0 0 20 20"><path d="M3 16l5-9 4 6 2-3 3 6z" fill="#fff"/></svg></span><div><h4>Hiking &amp; Outdoor</h4><p>Trails through hills and mountains</p></div></div>
    </div>
  </section>

  <section class="d-blog">
    <h2>Recent Blog</h2>
    <div class="d-row">
      <article class="d-post"><div class="photo" role="img" aria-label="Pasta being prepared in a kitchen" style="background:linear-gradient(135deg,#d7b48a,#a0623c)"></div><h4>Cooking Classes in Tuscany</h4><p>Learn traditional recipes with local chefs.</p><span class="btn">Read More</span></article>
      <article class="d-post"><div class="photo" role="img" aria-label="Table with Italian dishes" style="background:linear-gradient(135deg,#e2c9a3,#b4573a)"></div><h4>Top Italian Food Markets</h4><p>Where to find the freshest local produce.</p><span class="btn">Read More</span></article>
      <article class="d-post"><div class="photo" role="img" aria-label="Seaside village at dusk" style="background:linear-gradient(135deg,#7aa8c2,#d6a874)"></div><h4>Best Summer Beaches</h4><p>Our guide to the most beautiful coasts.</p><span class="btn">Read More</span></article>
    </div>
  </section>

  <section class="d-contact">
    <h2>Quick Contact</h2>
    <div class="d-form">
      <div class="field">Name</div><div class="field">Email</div>
      <div class="field msg">Message</div>
      <span class="btn">Send</span>
    </div>
  </section>

  <footer class="d-footer">
    <div class="d-footer-cols">
      <div class="brand"><span class="brand-dot"></span>HolidayNest</div>
      <div class="f-col"><h5>Quick Links</h5><ul><li>Home</li><li>Destinations</li><li>Villas</li><li>Blog</li></ul></div>
      <div class="f-col"><h5>Contacts</h5><ul><li>+39 055 010 2030</li><li>info@holidaynest.example</li><li>Via Verde 12, Florence</li></ul></div>
      <div class="f-col"><h5>Follow Us</h5><ul><li><span class="social-dot"></span>Social</li><li><span class="social-dot"></span>Photos</li><li><span class="social-dot"></span>Videos</li></ul></div>
    </div>
    <p class="copyright">© HolidayNest. All rights reserved.</p>
  </footer>
</main>

<!-- mobile layout -->
<main class="mobile">
  <header class="m-header">
    <div class="brand"><span class="brand-dot"></span>HolidayNest</div>
    <svg width="14" height="10" viewBox="0 0 14 10"><path d="M0 1h14M0 5h14M0 9h14" stroke="#1f2b2a" stroke-width="1.6"/></svg>
  </header>

  <section class="m-hero" role="img" aria-label="Lakeside Italian village with villas">
    <small>Holidays &amp; Vacation Homes</small>
    <h1>Villas in Italy</h1>
  </section>
  <div class="m-search">
    <h3>Find your Villa</h3>
    <div class="field">Destination</div>
    <div class="field-row"><div class="field">Check-in</div><div class="field">Check-out</div></div>
    <div class="field">Guests</div>
    <span class="btn">Search</span>
  </div>

  <section class="m-section m-best">
    <h2>Best Opportunity</h2>
    <div class="photo" role="img" aria-label="Villa with private swimming pool" style="background:linear-gradient(135deg,#c9a77e,#7ab3c8)"></div>
    <p>Villas with Private Pool</p>
    <div class="dots"><span class="on"></span><span></span><span></span></div>
  </section>

  <section class="m-exclusive">
    <small>Looking for an</small>
    <h2>Exclusive Holiday?</h2>
    <p>Discover luxury villas by the sea with private pools and tailored services.</p>
    <span class="btn">Discover More</span>
    <div class="photo" role="img" aria-label="Castle on a cliff above a turquoise bay" style="background:linear-gradient(160deg,#9bc3d6,#c7b28e 45%,#2e8fa6)"></div>
  </section>

  <section class="m-section m-dest">
    <h2>Destinations &amp; Tourist Areas</h2>
    <div class="photo" role="img" aria-label="Ancient amphitheatre" style="background:linear-gradient(135deg,#c9a074,#8fb1c9)"></div>
    <h4>Rome &amp; Lazio</h4>
    <p>History, art and fine food</p>
    <span class="btn">Discover</span>
    <div class="dots"><span class="on"></span><span></span><span></span></div>
  </section>

  <section class="m-section m-rentals">
    <span class="kicker">Our Villas in</span>
    <h2>Vacation Rentals</h2>
    <div class="photo" role="img" aria-label="Villa pool at sunset" style="background:linear-gradient(135deg,#3d7fa3,#d8a870)"></div>
    <div class="photo" role="img" aria-label="Stone villa with garden" style="background:linear-gradient(135deg,#b6a184,#6e8f5a)"></div>
    <div class="photo" role="img" aria-label="Infinity pool overlooking the sea" style="background:linear-gradient(135deg,#5fb6cf,#2f6f8e)"></div>
    <div class="photo" role="img" aria-label="Villa terrace at dusk" style="background:linear-gradient(135deg,#3a3f3a,#8b7257)"><span class="tag">Relax &amp; Pool</span></div>
    <div class="photo" role="img" aria-label="Sunny villa courtyard" style="background:linear-gradient(135deg,#e3c48f,#c98a4e)"></div>
  </section>

  <section class="m-section m-exp">
    <span class="kicker">Live Italy</span>
    <h2>Experiences or Activities</h2>
    <div class="exp"><span class="exp-icon"><svg width="10" height="10" viewBox="0 0 20 20"><path d="M10 2a6 6 0 0 1 6 6c0 4.5-6 10-6 10S4 12.5 4 8a6 6 0 0 1 6-6z" fill="none" stroke="#fff" stroke-width="2.4"/></svg></span><div><h4>Guided Tours</h4><p>Explore towns with local experts</p></div></div>
    <div class="exp"><span class="exp-icon"><svg width="10" height="10" viewBox="0 0 20 20"><path d="M4 10l4 4 8-8" fill="none" stroke="#fff" stroke-width="2.6"/></svg></span><div><h4>Wine &amp; Food Tasting</h4><p>Taste regional wines and dishes</p></div></div>
    <div class="exp"><span class="exp-icon"><svg width="10" height="10" viewBox="0 0 20 20"><circle cx="10" cy="10" r="7" fill="none" stroke="#fff" stroke-width="2.4"/></svg></span><div><h4>Boat Trips</h4><p>Sail along the coastline</p></div></div>
    <div class="exp"><span class="exp-icon"><svg width="10" height="10" viewBox="0 0 20 20"><path d="M3 16l5-9 4 6 2-3 3 6z" fill="#fff"/></svg></span><div><h4>Hiking &amp; Outdoor</h4><p>Trails through hills and mountains</p></div></div>
  </section>

  <section class="m-section m-blog">
    <h2>Recent Blog</h2>
    <div class="photo" role="img" aria-label="Pasta being prepared in a kitchen" style="background:linear-gradient(135deg,#d7b48a,#a0623c)"></div>
    <h4>Cooking Classes in Tuscany</h4>
    <p>Learn traditional recipes with local chefs.</p>
    <span class="btn">Read More</span>
  </section>

  <section class="m-section m-contact">
    <h2>Quick Contact</h2>
    <div class="field">Name</div>
    <div class="field">Email</div>
    <div class="field msg">Message</div>
    <span class="btn">Send</span>
  </section>

  <footer class="m-footer">
    <div class="f-col"><h5>Quick Links</h5><ul><li>Home</li><li>Destinations</li><li>Villas</li><li>Blog</li></ul></div>
    <div class="f-col"><h5>Contacts</h5><ul><li>+39 055 010 2030</li><li>info@holidaynest.example</li><li>Via Verde 12, Florence</li></ul></div>
    <div class="f-col"><h5>Follow Us</h5><ul><li><span class="social-dot"></span>Social</li><li><span class="social-dot"></span>Photos</li><li><span class="social-dot"></span>Videos</li></ul></div>
    <div class="brand"><span class="brand-dot"></span>HolidayNest</div>
  </footer>
</main>

</body>
</html>
```